****Business Card Design for Quarrystone Development. Design based around attached logo/company name

I’m looking for business card design for my company Quarrystone Development Group,LLC. Design should be professional, sharp and minimal. Outside of the attached logos, greyscale colors for remainder of cards. My thoughts are two-sided card with attached logo on one side and my info on the other but open to one-sided as well with right design.
Target Market(s)
Real estate professionals including banks, private investors, property owners, developers, commercial tenants like Brewlantern, Grovika or Tanquist’s.
Industry/Entity Type
Commercial real estate development and investments.
Contact Information for Business Card
Name, title, email, phone #’s, web address and physical address
Font styles to use
Other font styles liked:
- Helvetica, Garamond, etc
Colors
Designer to choose only greyscale colors for use in the design.
Requirements
Must have
- Attached logo first or second options.
Nice to have
- Two sided card with logo on one side. Attached Logo/company name can be laid out any way that flows as long as it’s legible.name
Should not have
- No loud colors. ***Please do not include logo, I have removed the company design with a logo image.

```html
<!DOCTYPE html>
<html lang="en">
<head>
<meta charset="utf-8">
<title>Quarrystone Development Group, LLC — Business Cards</title>
<link href="https://fonts.googleapis.com/css2?family=Marcellus&family=Tinos&family=Roboto:wght@400&display=swap" rel="stylesheet">
<style>
  :root{
    --backdrop:#2a2a2a;
    --card-light:#f7f7f7;
    --card-shade:#e6e6e8;
    --ink:#4a4e5a;
    --ink-soft:#5a5e68;
    --rule:#5e626c;
  }
  *{margin:0;padding:0;box-sizing:border-box;}
  html,body{width:1200px;height:1138px;overflow:hidden;background:var(--backdrop);}
  .canvas{position:relative;width:1200px;height:1138px;}
  .card{
    position:absolute;width:620px;height:376px;border-radius:16px;
    background:linear-gradient(160deg,var(--card-light) 0%,#f0f0f1 55%,var(--card-shade) 100%);
    overflow:hidden;color:var(--ink);
  }
  .card--front{left:272px;top:184px;}
  .card--back{left:274px;top:606px;}

  /* front */
  .wordmark{position:absolute;left:0;right:0;top:142px;text-align:center;font-family:"Marcellus",serif;}
  .wordmark__name{font-size:44px;letter-spacing:3px;line-height:1;display:inline-block;padding:0 4px 6px;border-bottom:1px solid var(--rule);}
  .wordmark__sub{font-size:16px;letter-spacing:3px;margin-top:8px;color:var(--ink-soft);}
  .front-web{position:absolute;left:0;right:0;top:518px;}
  .front-web{top:334px;display:flex;justify-content:center;align-items:center;gap:18px;
    font-family:"Roboto",sans-serif;font-size:14.5px;color:var(--ink-soft);}
  .front-web__rule{width:70px;height:3px;background:var(--rule);border-radius:2px;}

  /* back */
  .holder{position:absolute;left:42px;top:50px;}
  .holder__name{font-family:"Marcellus",serif;font-size:23px;letter-spacing:1px;line-height:1;}
  .holder__title{font-family:"Tinos",serif;font-size:15px;margin-top:8px;color:var(--ink-soft);}
  .address{position:absolute;left:42px;top:200px;font-family:"Tinos",serif;font-size:15px;line-height:22px;color:var(--ink-soft);}
  .contacts{position:absolute;left:42px;top:254px;list-style:none;font-family:"Tinos",serif;font-size:15px;color:var(--ink-soft);}
  .contacts li{display:flex;align-items:center;height:22px;}
  .contacts svg{width:12px;height:12px;margin-right:18px;fill:var(--ink-soft);}
  .vertical-mark{
    position:absolute;left:382px;top:160px;width:330px;height:64px;
    transform:rotate(-90deg);transform-origin:center;
    font-family:"Marcellus",serif;text-align:center;
  }
  .vertical-mark__name{font-size:39px;letter-spacing:3px;line-height:1;padding-bottom:4px;border-bottom:1px solid var(--rule);}
  .vertical-mark__sub{font-size:14px;letter-spacing:2.6px;margin-top:6px;color:var(--ink-soft);}
</style>
</head>
<body>
<main class="canvas">
  <section class="card card--front" aria-label="Card front">
    <div class="wordmark">
      <div class="wordmark__name">QUARRYSTONE</div>
      <div class="wordmark__sub">DEVELOPMENT GROUP, LLC</div>
    </div>
    <div class="front-web">
      <span class="front-web__rule"></span>
      <span>www.yourwebsite.com</span>
      <span class="front-web__rule"></span>
    </div>
  </section>

  <section class="card card--back" aria-label="Card back">
    <div class="holder">
      <div class="holder__name">JOHN DOE SMITH</div>
      <div class="holder__title">Managing Director</div>
    </div>
    <div class="address">234 Anywhere St., Any City,<br>Any Town, US 123456</div>
    <ul class="contacts">
      <li><svg viewBox="0 0 12 12"><path d="M1 4c0-2 2-3 5-3s5 1 5 3v1H8.5V4h-5v1H1z"/><rect x="2" y="6" width="8" height="5" rx="1"/></svg>828-111-1111</li>
      <li><svg viewBox="0 0 12 12"><rect x="0.5" y="2" width="11" height="8"/><path d="M1 2.5l5 4 5-4" fill="none" stroke="#f2f2f2" stroke-width="1.2"/></svg>john@yourwebsite.com</li>
      <li><svg viewBox="0 0 12 12"><circle cx="6" cy="6" r="5.5"/><path d="M0.5 6h11M6 0.5v11M2 3h8M2 9h8" stroke="#f2f2f2" stroke-width="0.8" fill="none"/></svg>www.yourwebsite.com</li>
    </ul>
    <div class="vertical-mark">
      <div class="vertical-mark__name">QUARRYSTONE</div>
      <div class="vertical-mark__sub">DEVELOPMENT GROUP, LLC</div>
    </div>
  </section>
</main>
</body>
</html>
```